KLV Plant Services

We are a heavy diesel mechanical business with additional air con certificates, remapping engine rebuilt

Contact Information for Business Card

Company Name, Director Name, Managing Director, Contact details, email and website

Font styles to use
Serif
Script

```html
<!DOCTYPE html>
<html lang="en">
<head>
<meta charset="utf-8">
<title>KLV Plant Services – Business Card</title>
<link rel="stylesheet" href="https://fonts.googleapis.com/css2?family=Libre+Baskerville:wght@400;700&family=Great+Vibes&display=swap">
<style>
  :root {
    --stage: #e9e4dc;
    --front-blue: #1a1c7a;
    --back-charcoal: #2b2b31;
    --ink-white: #ffffff;
    --accent-blue: #5b63e6;
    --shadow: rgba(40, 30, 20, 0.28);
    --serif: "Libre Baskerville", Georgia, serif;
    --script: "Great Vibes", cursive;
  }
  * { margin: 0; padding: 0; box-sizing: border-box; }
  html, body { width: 1200px; height: 675px; overflow: hidden; }
  body {
    background: var(--stage);
    font-family: var(--serif);
    display: flex;
    align-items: center;
    justify-content: center;
    gap: 90px;
  }
  .card {
    border-radius: 26px;
    box-shadow: 0 14px 30px var(--shadow);
    color: var(--ink-white);
    position: relative;
    flex: none;
  }
  .brand-ring {
    border: 4px solid var(--ink-white);
    border-radius: 50%;
    flex: none;
  }
  .brand-name {
    font-family: var(--serif);
    font-weight: 700;
    color: var(--ink-white);
    white-space: nowrap;
  }
  /* Front */
  .card-front {
    width: 540px;
    height: 320px;
    background: var(--front-blue);
    display: flex;
    align-items: center;
    justify-content: center;
    gap: 16px;
  }
  .card-front .brand-ring { width: 32px; height: 32px; }
  .card-front .brand-name { font-size: 32px; }
  /* Back */
  .card-back {
    width: 320px;
    height: 540px;
    background: var(--back-charcoal);
    padding: 62px 30px 40px;
    display: flex;
    flex-direction: column;
    align-items: flex-end;
  }
  .back-brand {
    align-self: center;
    display: flex;
    align-items: center;
    gap: 9px;
    margin-bottom: 130px;
  }
  .back-brand .brand-ring { width: 20px; height: 20px; border-width: 3px; }
  .back-brand .brand-name { font-size: 20px; }
  .holder-name {
    font-family: var(--serif);
    font-weight: 700;
    font-size: 23px;
    color: var(--accent-blue);
    text-align: right;
    white-space: nowrap;
  }
  .holder-role {
    font-family: var(--script);
    font-size: 24px;
    line-height: 1.1;
    margin-top: 4px;
    text-align: right;
  }
  .contact-list {
    list-style: none;
    margin-top: 20px;
    font-size: 12px;
    line-height: 1.65;
    text-align: right;
  }
  .contact-list li {
    display: flex;
    justify-content: flex-end;
    align-items: center;
    gap: 10px;
    white-space: nowrap;
  }
  .contact-list .address { display: block; margin-bottom: 12px; }
  .contact-icon { width: 12px; height: 12px; flex: none; }
</style>
</head>
<body>
  <section class="card card-front" aria-label="Business card front">
    <span class="brand-ring" aria-hidden="true"></span>
    <span class="brand-name">KLV Plant Services</span>
  </section>

  <section class="card card-back" aria-label="Business card back">
    <div class="back-brand">
      <span class="brand-ring" aria-hidden="true"></span>
      <span class="brand-name">KLV Plant Services</span>
    </div>
    <h1 class="holder-name">DIRECTOR NAME</h1>
    <p class="holder-role">Managing Director</p>
    <ul class="contact-list">
      <li class="address">P.O. Box, Street Name,<br>Countryname , ZIPCODE 0000</li>
      <li>845 845 8456
        <svg class="contact-icon" viewBox="0 0 12 12" aria-hidden="true"><path d="M2 1h2.5l1 3-1.5 1a6 6 0 0 0 3 3l1-1.5 3 1V10a1 1 0 0 1-1 1A9 9 0 0 1 1 2a1 1 0 0 1 1-1z" fill="#fff"/></svg>
      </li>
      <li>458 458 4569
        <svg class="contact-icon" viewBox="0 0 12 12" aria-hidden="true"><rect x="3" y="0.8" width="6" height="10.4" rx="1" fill="none" stroke="#fff" stroke-width="1.2"/></svg>
      </li>
      <li>info@websitename.com
        <svg class="contact-icon" viewBox="0 0 12 12" aria-hidden="true"><rect x="0.5" y="2.5" width="11" height="7" fill="#fff"/><path d="M0.5 2.5 6 6.5l5.5-4" fill="none" stroke="#2b2b31" stroke-width="1"/></svg>
      </li>
      <li>www.websitename.com
        <svg class="contact-icon" viewBox="0 0 12 12" aria-hidden="true"><g fill="none" stroke="#fff" stroke-width="1"><circle cx="6" cy="6" r="5"/><ellipse cx="6" cy="6" rx="2.2" ry="5"/><path d="M1 6h10"/></g></svg>
      </li>
    </ul>
  </section>
</body>
</html>
```